W. Darrow Billboard

2 miles ahead on right
Voted number 1 ... again!
California cuisine
Located in Historic Marbury Hill Inn
Picture of a couple dining
www.torvellis.com 555.317.2968

Target Market(s)

travelers

Industry/Entity Type

hospitality

Font styles to use
Serif

Colors
59FF00
82FF00
B8FF75
E3FFCB
F4FFEA
EE7325
F08F49
F5BC92
FAE3D3
FDF4ED

Requirements
Should not have
• bright colors

```html
<!DOCTYPE html>
<html lang="en">
<head>
<meta charset="utf-8">
<title>W. Darrow Billboard</title>
<link rel="stylesheet" href="https://fonts.googleapis.com/css2?family=Playfair+Display:wght@700;900&family=Rubik:wght@800&family=Roboto+Condensed:wght@700&family=Open+Sans:wght@500&display=swap">
<style>
  :root {
    --board: #fbfbf0;
    --red: #c81521;
    --deep-red: #9a1c1c;
    --orange: #e8481c;
    --green: #8cc63f;
    --lime: #a8d932;
    --ink: #2b2b2b;
    --photo-warm: #c99a5e;
    --photo-cool: #5f7a6a;
  }
  * { margin: 0; padding: 0; box-sizing: border-box; }
  html, body { width: 1200px; height: 801px; overflow: hidden; background: #e9e9e4; }
  .billboard {
    position: relative;
    width: 1200px;
    height: 801px;
    background: var(--board);
    overflow: hidden;
  }
  .corner-bands { position: absolute; inset: 0; }
  .brand {
    position: absolute;
    left: 130px;
    top: 40px;
    color: var(--orange);
    font-family: "Playfair Display", serif;
    font-weight: 900;
  }
  .brand-name { font-size: 120px; line-height: 1; letter-spacing: 1px; }
  .brand-sub { font-size: 34px; letter-spacing: 6px; margin-left: 120px; line-height: 1.2; }
  .tagline {
    position: absolute;
    left: 150px;
    top: 260px;
    color: var(--lime);
    font-family: "Playfair Display", serif;
    font-weight: 900;
    font-size: 54px;
  }
  .headline {
    position: absolute;
    left: 120px;
    top: 335px;
    color: var(--deep-red);
    font-family: "Rubik", sans-serif;
    font-weight: 800;
    text-transform: uppercase;
    line-height: 0.95;
    letter-spacing: 6px;
  }
  .headline-line { display: block; font-size: 92px; }
  .headline-line.second { margin-left: 110px; }
  .location {
    position: absolute;
    left: 240px;
    top: 540px;
    color: var(--ink);
    font-family: "Open Sans", sans-serif;
    font-weight: 500;
    font-size: 34px;
  }
  .phone {
    position: absolute;
    left: 230px;
    top: 600px;
    color: var(--red);
    font-family: "Roboto Condensed", sans-serif;
    font-weight: 700;
    font-size: 66px;
    letter-spacing: 3px;
  }
  .website {
    position: absolute;
    right: 110px;
    bottom: 60px;
    color: var(--red);
    font-family: "Roboto Condensed", sans-serif;
    font-weight: 700;
    font-size: 56px;
    letter-spacing: 2px;
  }
  .award {
    position: absolute;
    left: 770px;
    top: 210px;
    width: 200px;
    height: 220px;
  }
  .award-text {
    position: absolute;
    inset: 0;
    text-align: center;
    color: #fff;
    font-family: "Playfair Display", serif;
    font-weight: 700;
  }
  .award-voted { margin-top: 14px; font-size: 24px; }
  .award-stars { font-size: 16px; letter-spacing: 4px; margin-top: 2px; }
  .award-number { font-size: 72px; line-height: 0.9; display: inline-block; }
  .award-again { font-size: 24px; color: #ffe45c; display: inline-block; margin-left: 4px; }
  .dining-photo {
    position: absolute;
    left: 720px;
    top: 420px;
    width: 400px;
    height: 250px;
    border-radius: 90px 0 0 90px;
    background: linear-gradient(135deg, var(--photo-cool) 0%, #8f8a6c 45%, var(--photo-warm) 100%);
  }
</style>
</head>
<body>
<main class="billboard">
  <svg class="corner-bands" width="1200" height="801" viewBox="0 0 1200 801" aria-hidden="true">
    <polygon points="0,0 230,0 0,90" fill="var(--red)"/>
    <polygon points="0,90 230,0 300,0 0,150" fill="var(--green)"/>
    <polygon points="0,150 300,0 340,0 0,190" fill="#e4e4dc"/>
    <polygon points="0,801 260,801 0,640" fill="var(--red)"/>
    <polygon points="0,640 260,801 200,801 0,560" fill="var(--green)" opacity="0"/>
    <polygon points="0,560 0,640 230,801 300,801" fill="var(--green)"/>
    <polygon points="0,520 0,560 300,801 340,801" fill="#e4e4dc"/>
    <polygon points="1200,0 1200,160 1030,0" fill="var(--red)"/>
    <polygon points="1030,0 1200,160 1200,220 980,0" fill="var(--green)"/>
    <polygon points="1200,801 1200,690 1020,801" fill="var(--red)"/>
    <polygon points="1200,690 1200,640 940,801 1020,801" fill="var(--green)"/>
  </svg>

  <div class="brand">
    <div class="brand-name">Torvelli's</div>
    <div class="brand-sub">SOUTHWEST BAR &amp; GRILL</div>
  </div>

  <p class="tagline">Good Food, Good Life</p>

  <h1 class="headline">
    <span class="headline-line">California</span>
    <span class="headline-line second">Cuisine</span>
  </h1>

  <p class="location">Historic Marbury Hill Inn</p>
  <p class="phone">555.317.2968</p>

  <div class="award">
    <svg width="200" height="220" viewBox="0 0 200 220" aria-hidden="true">
      <polygon points="0,0 200,0 190,40 200,80 175,80 175,220 100,185 25,220 25,80 0,80 10,40" fill="var(--red)"/>
    </svg>
    <div class="award-text">
      <div class="award-voted">Voted Number</div>
      <div class="award-stars">★★★★★</div>
      <div><span class="award-number">1</span><span class="award-again">again!</span></div>
    </div>
  </div>

  <div class="dining-photo" role="img" aria-label="Photo of a couple dining together at a restaurant table"></div>

  <p class="website">www.torvellis.com</p>
</main>
</body>
</html>
```